July 2022 Industrial Manufacturer Product Expo Mexico City

We manufacture large screws and fastners for large Mining equipment, Trains, large ships, airplanes, wind turbines, and so on. We also do custom work base on the customer needs. No matter the size we can make it.
We have a Expo coming up with companies all over the world. We have to stand out we are a family own business so our customer service will be above and beyond anyone can provide. We do not have a sales force to push our products and services we provide one on one service.
Plus@!! I'm looking for anything that you designers can come up with if it was your company to put on a business card, plus i want to do a 1 or 2 sided pamphlet, and then a website. We make Speciality Bolts for large mining equipment these bolts can be 3 to 4 foot long!!! Plus fasteners, Nuts, washers, any, size, strengths, special materials, we offer more of a ono on one customer service, We are a small company, family own, but can fulfill any type of orders. We can also provide special time lines for emergency orders. "We keep the machines running we here at KRV don't believe in down time" We want to hear any slogan based on our company to stand out.
Thanks i really appreciate all your work and options that we have to pick on. Plus just a thought we could possibly want to entertain a experience Marketing internet help maybe a employment possibility. Thanks

I need 2 cards one in Spanish and English Like the steel back ground maybe send me in some bright red and blue writing Same with the Black cards Please remove the word Military The logo KRV maybe integrate a picture of a Bolt 🔩 Thank you

Still looking for I need 2 cards one in Spanish and English Like the steel back ground maybe send me in some bright red and blue writing Same with the Black cards try bright writing Please remove the word Military The logo KRV maybe integrate a picture of a Bolt 🔩 Plus will need the company to make a brochure and website next Thank you

Target Market(s)

Large Mining, Ship, Train, Green Energy, VELM, and Government equipment. Throughout the World

Industry/Entity Type

We can Custom Manufacture any type of Fastners for Mining equipment, Trains, Ships, Green energy, Governments, or military projects. wind turbines,

Contact Information for Business Card

I attached the name and contact info that's on a card, plus the Company Logo. Would like industrial looking background with Bright Colors that will stand out!! If we can insert somewhere maybe on back that we "Custom Manufacture Any Size or Quantity Fastners for Large Mining Equipment, Trains, Ships, Green Energy Equipment or Government Projects

Font styles to use
Other font styles liked:
• You Pick, has to be bold, colorful standout, Professional looking Beable to read it.

Colors

Designer to choose colors to be used in the design.

Requirements
Must have
• Need in Spanish and English TO STANDOUT FROM THE REST OF THE EXPO!! See Business card details, Rounded corners
Nice to have
• Can i see some of the darker cards with Bright Red and Blue letters I like to see the different type of card material, heavy thickness, plastic, transparent, Metal types, Bright Colors, I saw like Raised letters like on the logo.

```html
<!DOCTYPE html>
<html lang="es">
<head>
<meta charset="utf-8">
<title>KRV – Business Cards / Tarjetas de presentación</title>
<link rel="stylesheet" href="https://fonts.googleapis.com/css2?family=Roboto+Condensed:wght@400;700&display=swap">
<style>
  :root {
    --bg: #2a2a2c;
    --card-white: #f7f7f5;
    --steel-light: #eef1f4;
    --steel-mid: #b9c0c8;
    --steel-dark: #8c949e;
    --blue-bright: #0a6fe0;
    --blue-deep: #07208e;
    --blue-text: #1b3fa6;
    --red-bright: #e1121b;
    --graphite: #3b3d42;
    --gray-text: #55575c;
  }
  * { box-sizing: border-box; margin: 0; padding: 0; }
  html, body {
    width: 1200px; height: 874px; overflow: hidden;
    background: var(--bg);
    font-family: "Roboto Condensed", "Arial Narrow", sans-serif;
  }
  .card {
    position: absolute;
    left: 300px;
    width: 600px; height: 340px;
    border-radius: 26px;
    overflow: hidden;
    box-shadow: 0 18px 40px rgba(0,0,0,.45);
  }
  .wordmark {
    font-weight: 700;
    letter-spacing: 6px;
    line-height: 1;
  }

  /* front – English, brushed steel */
  .card-front {
    top: 60px;
    background:
      repeating-linear-gradient(0deg, rgba(255,255,255,.18) 0 1px, rgba(0,0,0,.04) 1px 3px),
      linear-gradient(160deg, var(--steel-light) 0%, var(--steel-mid) 45%, var(--steel-light) 70%, var(--steel-dark) 100%);
  }
  .card-front .brand {
    position: absolute; left: 0; right: 0; top: 70px;
    text-align: center;
  }
  .card-front .wordmark { font-size: 104px; color: var(--blue-bright); }
  .card-front .tagline {
    margin-top: 12px;
    font-size: 19px; font-weight: 700; letter-spacing: 1px;
    color: var(--red-bright);
  }
  .card-front .claim {
    position: absolute; left: 60px; right: 60px; bottom: 34px;
    text-align: center;
    font-size: 14px; line-height: 19px;
    color: var(--blue-deep);
  }

  /* back – Spanish, white */
  .card-back {
    top: 440px;
    background: var(--card-white);
  }
  .card-back .brand {
    position: absolute; left: 56px; top: 36px;
  }
  .card-back .wordmark { font-size: 86px; color: var(--graphite); }
  .card-back .rule {
    width: 300px; height: 3px; margin-top: 6px;
    background: var(--red-bright);
  }
  .card-back .tagline {
    margin-top: 6px;
    font-size: 15px; font-weight: 700; letter-spacing: .6px;
    color: var(--blue-text);
  }
  .contact {
    position: absolute; left: 44px; top: 196px;
    list-style: none;
    font-size: 15px; color: var(--gray-text);
    line-height: 21px;
  }
  .contact li { display: flex; align-items: center; gap: 8px; }
  .contact svg { width: 13px; height: 13px; flex: none; fill: var(--red-bright); }
  .name-band {
    position: absolute; left: 300px; right: 0; top: 232px;
    height: 80px;
    border-radius: 40px 0 0 40px;
    background: linear-gradient(90deg, var(--blue-deep) 0%, #1f7fd6 45%, var(--blue-deep) 100%);
    border-top: 3px solid var(--red-bright);
    color: #fff;
    padding: 12px 34px 0 34px;
    text-align: right;
  }
  .name-band .person { font-size: 21px; font-weight: 700; white-space: nowrap; }
  .name-band .role { font-size: 14px; margin-top: 3px; white-space: nowrap; }
</style>
</head>
<body>

<section class="card card-front" lang="en" aria-label="Card front, English">
  <div class="brand">
    <div class="wordmark">KRV</div>
    <div class="tagline">BOLT MANUFACTURING &amp; DISTRIBUTION</div>
  </div>
  <p class="claim">Custom manufacture of any size or quantity fasteners for large mining equipment, trains, ships, green energy and government projects</p>
</section>

<section class="card card-back" aria-label="Reverso de la tarjeta, español">
  <div class="brand">
    <div class="wordmark">KRV</div>
    <div class="rule"></div>
    <div class="tagline">FABRICACION Y DISTRIBUCION DE TORNILLOS</div>
  </div>

  <ul class="contact">
    <li>
      <svg viewBox="0 0 16 16" aria-hidden="true"><path d="M3.6 1.2 6 3.6 4.7 5.3c.8 2 2.4 3.6 4.4 4.4L10.7 8.4l2.4 2.4-1.5 2.6C6.4 13.2 2.8 9.6 1 4.4z"/></svg>
      5550142387
    </li>
    <li>
      <svg viewBox="0 0 16 16" aria-hidden="true"><path d="M4 1h8v14H4zM5.5 2.5v10h5v-10z"/></svg>
      5550198264
    </li>
    <li>
      <svg viewBox="0 0 16 16" aria-hidden="true"><path d="M1 3h14v10H1zM2.5 4.5 8 8.5l5.5-4z"/></svg>
      krv.ventas@ejemplo.com
    </li>
  </ul>

  <div class="name-band">
    <div class="person">Lic. Marisol Ortega Vidal</div>
    <div class="role">Cotizaciones en tornillería · Quotes &amp; Sales</div>
  </div>
</section>

</body>
</html>
```